Adelaide based cleaning and remediation business needs a website design

We are launching a new company with no clients as yet so we don't have the benefit of Plimora Reviews to build confidence. We can use our  past work history with other employers in the industry to give some credibility. Happy to use any colour scheme as long as it look interesting when people click on the site it gets there attention. enquiry . I have supplied a mock up the important information and various photos as they tell a lot of the story.

```html
<!DOCTYPE html>
<html lang="en">
<head>
<meta charset="utf-8">
<title>Kestrel Services Pty Ltd</title>
<link href="https://fonts.googleapis.com/css2?family=Lato:wght@400;700;900&display=swap" rel="stylesheet">
<style>
:root{
  --teal:#3fa3b8;
  --teal-dark:#2f8ea3;
  --green:#a6c44a;
  --ink:#111;
  --grey:#6d6d6d;
  --white:#fff;
  --black:#000;
}
*{box-sizing:border-box;margin:0;padding:0}
html,body{width:1200px;height:4035px;overflow:hidden;background:var(--white)}
body{position:relative;font-family:'Lato',sans-serif;color:var(--ink)}
.abs{position:absolute}
.flex{display:flex;align-items:center}

/* header */
.topbar{left:99px;top:24px;gap:40px;font-size:16px;color:var(--grey)}
.topbar span{display:flex;align-items:center;gap:12px}
.rule{top:72px;height:1px;background:#d8d8d8}
.brand{left:525px;top:14px;width:150px;height:140px;display:flex;flex-direction:column;align-items:center;justify-content:center;gap:8px}
.brand .mark{width:34px;height:34px;border:2px solid var(--ink)}
.brand b{font-size:20px;font-weight:900;letter-spacing:1px}
.social{gap:6px}
.social i{display:block;width:34px;height:34px;border-radius:50%;border:2px solid var(--ink)}
.social.top i:nth-child(1){border-color:#c13584}
.social.top i:nth-child(2),.social.top i:nth-child(5){border-color:#3b6fb6}
.social.top i:nth-child(4){border-color:#d93025}
.nav{top:106px;font-size:16px;color:#222}
.nav a{position:absolute;white-space:nowrap;text-decoration:none;color:inherit}

/* hero */
.hero{left:0;top:168px;width:1200px;height:600px;background:linear-gradient(120deg,#3a3a33 0%,#56554d 40%,#bdbdb8 62%,#4a463e 100%)}
.hero h1{position:absolute;left:100px;top:165px;font-size:64px;line-height:78px;font-weight:900;color:var(--white)}
.hero .btn{position:absolute;left:100px;top:333px;width:232px;height:66px;background:var(--teal);color:var(--white);font-weight:700;font-size:17px;display:flex;align-items:center;justify-content:center}
.circ-arrow{width:44px;height:44px;border-radius:50%;background:#111;display:flex;align-items:center;justify-content:center}

/* headings */
.h2{left:0;width:1200px;text-align:center;font-size:35px;font-weight:900;text-transform:uppercase;letter-spacing:-.5px}
.bar{height:4px;width:75px;background:var(--green)}

/* service cards */
.card{top:967px;width:321px;height:355px;border-radius:20px;overflow:hidden}
.card p{position:absolute;left:30px;bottom:20px;color:var(--white);font-weight:700;font-size:22px;line-height:30px;text-transform:uppercase}

/* testimonial */
.band{left:0;top:1449px;width:1200px;height:661px;background:linear-gradient(180deg,#4ea6a8 0%,#7db07a 55%,#a2bf53 100%)}
.band h2{position:absolute;top:68px;width:1200px;text-align:center;color:var(--white);font-size:35px;line-height:52px;font-weight:900}
.quote{left:230px;top:1675px;width:741px;height:333px;background:var(--white);border-radius:20px;text-align:center}
.quote p{margin:32px 60px 0;font-size:16px;line-height:26px}
.avatars{justify-content:center;gap:0;margin-top:20px}
.avatars i{display:block;border-radius:50%;background:#b9bcbd;border:3px solid var(--white)}
.quote h4{margin-top:22px;font-size:21px;font-weight:700}
.pill{width:44px;height:44px;border-radius:50%;background:var(--teal);border:3px solid var(--white);display:flex;align-items:center;justify-content:center}

/* circles */
.blob{top:2330px;width:323px;height:323px;border-radius:50%;color:var(--white);text-align:center;display:flex;flex-direction:column;align-items:center;padding:0 38px}
.blob h3{font-size:17px;line-height:22px;font-weight:900;text-transform:uppercase;margin-bottom:18px}
.blob p{font-size:12px;line-height:16px}

/* faq */
.faqband{left:0;top:2765px;width:1200px;height:721px;background:linear-gradient(180deg,#3fa3b8 0%,#7eb6a0 45%,#a8c64c 100%)}
.faq-title{left:100px;top:2828px;color:var(--white);font-size:36px;font-weight:900}
.acc{left:100px;width:497px;background:var(--white);border-radius:18px;padding:0 36px}
.acc h4{font-size:21px;font-weight:700;display:flex;justify-content:space-between;align-items:center}
.acc h4 i{display:flex;width:28px;height:28px;border-radius:50%;border:1.5px solid var(--teal);color:var(--teal);align-items:center;justify-content:center;font-style:normal;font-size:20px;font-weight:400}
.acc p{font-size:14px;line-height:21px;color:var(--grey);margin-top:14px}
.cards-label{left:103px;top:3353px;font-size:20px;font-weight:700}
.paycards{left:103px;top:3392px;gap:4px}
.paycards span{width:77px;height:50px;background:var(--white);border:2px solid #ddd;font-size:13px;font-weight:700;display:flex;align-items:center;justify-content:center}
.photo-roof{left:672px;top:2859px;width:429px;height:544px;border-radius:20px;background:linear-gradient(180deg,#b6a27a 0%,#8c7a5e 35%,#3a3a38 60%,#1e1e1e 100%)}

/* footer */
.footer{left:0;top:3486px;width:1200px;height:549px;background:var(--black);color:var(--white)}
.footer h3{position:absolute;font-size:26px;font-weight:700}
.footer .line{position:absolute;font-size:15px;line-height:25px;display:flex;gap:14px;align-items:flex-start}
.flogo{left:99px;top:67px;width:196px;height:238px;display:flex;flex-direction:column;align-items:center;justify-content:center;gap:12px}
.flogo .mark{width:46px;height:46px;border:2px solid var(--white)}
.flogo b{font-size:26px;font-weight:900;letter-spacing:1px}
.badge{left:100px;top:352px;width:88px;height:88px;border-radius:50%;background:#4e8f7a}
.social.foot i{border-color:var(--white)}
.green{color:var(--green)}
</style>
</head>
<body>

<!-- header -->
<div class="abs flex topbar">
  <span>
    <svg width="32" height="22" viewBox="0 0 32 22"><rect x="1" y="1" width="30" height="20" fill="none" stroke="#a6c44a" stroke-width="2"/><path d="M1 1l15 11L31 1" fill="none" stroke="#a6c44a" stroke-width="2"/></svg>
    info@kestrelclean.com
  </span>
  <span>
    <svg width="24" height="24" viewBox="0 0 24 24"><path d="M5 2l4 1 1 5-3 2a13 13 0 0 0 7 7l2-3 5 1 1 4c-1 3-3 3-5 3C9 21 3 15 3 7c0-2 0-4 2-5z" fill="#a6c44a"/></svg>
    +1 555-010-0199
  </span>
</div>
<div class="abs rule" style="left:99px;width:426px"></div>
<div class="abs rule" style="left:675px;width:426px"></div>
<div class="abs brand"><span class="mark"></span><b>KESTREL</b></div>
<div class="abs flex social top" style="left:896px;top:18px" aria-label="Social media links"><i></i><i></i><i></i><i></i><i></i></div>
<nav class="abs nav" style="left:0;width:1200px">
  <a style="left:99px;color:var(--teal)">Home</a>
  <a style="left:210px">About Us</a>
  <a style="left:346px">Our Services</a>
  <a style="left:697px">Why Choose Kestrel</a>
  <a style="left:908px">Contact Us</a>
  <svg style="position:absolute;left:1074px;top:-2px" width="26" height="26" viewBox="0 0 26 26"><circle cx="11" cy="11" r="8" fill="none" stroke="#111" stroke-width="2.2"/><path d="M17 17l7 7" stroke="#111" stroke-width="2.2"/></svg>
</nav>

<!-- hero -->
<section class="abs hero" role="img" aria-label="Worker in a white protective suit and respirator cleaning a dusty roof space">
  <h1>KESTREL<br>SERVICES PTY LTD</h1>
  <div class="btn">DIRTY JOB CLEANERS</div>
  <div class="abs circ-arrow" style="left:36px;top:242px"><svg width="14" height="14" viewBox="0 0 14 14"><path d="M9 2L4 7l5 5" fill="none" stroke="#a6c44a" stroke-width="2"/></svg></div>
  <div class="abs circ-arrow" style="left:1114px;top:242px"><svg width="14" height="14" viewBox="0 0 14 14"><path d="M5 2l5 5-5 5" fill="none" stroke="#a6c44a" stroke-width="2"/></svg></div>
</section>

<!-- signature services -->
<h2 class="abs h2" style="top:866px">Our Signature Services</h2>
<div class="abs bar" style="left:562px;top:925px"></div>
<div class="abs card" style="left:99px;background:linear-gradient(160deg,#8a6d4a,#4a3a2a)" role="img" aria-label="Cluttered storeroom shelves full of belongings"><p>End of lease &amp; estate<br>clean ups squalor<br>clean ups</p></div>
<div class="abs card" style="left:439px;background:linear-gradient(180deg,#9cc6cf 0%,#5fb1c2 60%,#3fa3b8 100%)" role="img" aria-label="Pigeons perched on a ledge above a droppings-stained wall"><p>Pigeon waste<br>clean ups</p></div>
<div class="abs card" style="left:779px;background:linear-gradient(170deg,#6b5a55,#2e2a28 55%,#4a4642)" role="img" aria-label="Fire damaged kitchen with burnt ceiling insulation"><p>Fire damage clean outs</p></div>

<!-- testimonial -->
<section class="abs band" role="img" aria-label="Faded background of a cluttered room covered in debris">
  <h2>ONLY THE BEST SERVICE FOR<br>OUR CUSTOMERS</h2>
  <div class="abs bar" style="left:562px;top:166px;background:var(--green)"></div>
  <div class="abs pill" style="left:210px;top:391px"><svg width="12" height="14" viewBox="0 0 12 14"><path d="M8 2L3 7l5 5" fill="none" stroke="#fff" stroke-width="2.2"/></svg></div>
  <div class="abs pill" style="left:945px;top:391px"><svg width="12" height="14" viewBox="0 0 12 14"><path d="M4 2l5 5-5 5" fill="none" stroke="#fff" stroke-width="2.2"/></svg></div>
</section>
<div class="abs quote">
  <p>Daniel and his team arrived the next morning to clean up a rental property my husband and I own which and had been trashed by the tenants.<br>He was the only contractor to return my call. They did an amazing job and also deodorised the house for no extra charge.</p>
  <div class="flex avatars" aria-label="Customer portraits">
    <i style="width:62px;height:62px"></i>
    <i style="width:86px;height:86px;border-color:var(--green);background:#8fa7b3"></i>
    <i style="width:62px;height:62px"></i>
  </div>
  <h4>Maren Holloway, Satisfied customer</h4>
</div>

<!-- circles -->
<h2 class="abs h2" style="top:2212px">We do the stuff nobody wants to do</h2>
<div class="abs bar" style="left:562px;top:2270px"></div>
<div class="abs blob" style="left:99px;background:var(--teal);padding-top:38px">
  <h3>Pigeon waste</h3>
  <p>Can cause damage to buildings and spread disease, mites and bacteria, triggering alarms and damaging the reputation of businesses.<br><br>1. The pigeon faeces is carefully removed by our trained operatives, who also dispose of it in an environmentally friendly way.<br>2. Next, in order to remove stains and ensure safety, we use eco-friendly chemicals to clean and disinfect the impacted areas.</p>
</div>
<div class="abs blob" style="left:439px;background:radial-gradient(circle,#a6c44a 55%,#98b83e 100%);padding-top:80px">
  <h3>Fire damage clean<br>outs</h3>
  <p>Removal of debris; On site cleaning of contents; Cleaning of carpets and upholstered items; Catalogue all contents for packing and storage Pressure cleaning of contaminated surfaces;</p>
</div>
<div class="abs blob" style="left:779px;background:var(--teal);padding-top:38px">
  <h3>Squlaor estate<br>clean ups</h3>
  <p>Kestrel Services is a hoarding clean up firm that approaches clutter removal personally. We always operate with compassion, prioritising the individuals involved over the cleaning procedure, and we understand the psychology of a person's hoarding attitude. We provide the following services</p>
</div>

<!-- faq -->
<div class="abs faqband"></div>
<div class="abs faq-title">FAQS</div>
<div class="abs bar" style="left:100px;top:2886px"></div>
<div class="abs acc" style="top:2922px;height:222px;padding-top:26px">
  <h4>About Us <i>−</i></h4>
  <p>Adelaide-based Kestrel Services is a family-run organisation.We have been in operation for more than two decades.We've gained some knowledge about cleaning and squalor removal services throughout the years. As a small South Australian company, we base everything on responsibility honesty and fairness.We are aware of the confidence you put in us when you seek our help</p>
</div>
<div class="abs acc flex" style="top:3168px;height:59px"><h4 style="width:100%">Pricing <i>+</i></h4></div>
<div class="abs acc flex" style="top:3250px;height:60px"><h4 style="width:100%">Qualifications <i>+</i></h4></div>
<div class="abs cards-label">We accept all major credit cards</div>
<div class="abs flex paycards" aria-label="Accepted payment cards">
  <span>Amberline</span><span>Circlepay</span><span>Vantra</span><span>Wayfind</span>
</div>
<div class="abs photo-roof" role="img" aria-label="Worker in protective suit cleaning a gravel-covered roof gutter"></div>

<!-- footer -->
<footer class="abs footer">
  <div class="abs flogo"><span class="mark"></span><b>KESTREL</b></div>
  <div class="abs badge" aria-label="Certification badge"></div>

  <h3 style="left:432px;top:70px">Contact Us</h3>
  <div class="line" style="left:424px;top:128px">
    <svg width="18" height="22" viewBox="0 0 18 22"><path d="M9 21s7-7 7-12A7 7 0 0 0 2 9c0 5 7 12 7 12z" fill="none" stroke="#a6c44a" stroke-width="1.6"/><circle cx="9" cy="9" r="2.5" fill="none" stroke="#a6c44a" stroke-width="1.6"/></svg>
    12 Wattle Lane Norwood SA5067</div>
  <div class="line" style="left:424px;top:175px">
    <svg width="20" height="20" viewBox="0 0 24 24"><path d="M5 2l4 1 1 5-3 2a13 13 0 0 0 7 7l2-3 5 1 1 4c-1 3-3 3-5 3C9 21 3 15 3 7c0-2 0-4 2-5z" fill="none" stroke="#a6c44a" stroke-width="1.6"/></svg>
    Call: Daniel or Tomas 0400 555 019</div>
  <div class="line" style="left:424px;top:227px">
    <svg width="20" height="16" viewBox="0 0 20 16"><rect x="1" y="1" width="18" height="14" fill="none" stroke="#a6c44a" stroke-width="1.6"/><path d="M1 1l9 7 9-7" fill="none" stroke="#a6c44a" stroke-width="1.6"/></svg>
    Email: admin@kestrelservices.com</div>
  <div class="line" style="left:430px;top:282px;width:360px">Got more questions about our clean-up services and what we offer?Get in touch today M 0400 555 019</div>

  <h3 style="left:432px;top:352px">Get a Quick Quote</h3>
  <div class="line" style="left:436px;top:400px;display:block">Send a text to Kestrel Services<br>Please enteryour mobile number or email and message<br><span class="green" style="font-size:17px;line-height:34px">0400555019</span></div>

  <h3 style="left:869px;top:70px">Business Hours</h3>
  <div class="line" style="left:869px;top:128px">
    <svg width="24" height="24" viewBox="0 0 24 24"><circle cx="12" cy="12" r="10" fill="none" stroke="#a6c44a" stroke-width="1.6"/><path d="M12 6v6l4 3" fill="none" stroke="#a6c44a" stroke-width="1.6"/></svg>
    <span>Mondayto Saturday 8:00<br>am to 4:00 pm</span></div>
  <h3 style="left:869px;top:220px">Follow Us</h3>
  <div class="abs flex social foot" style="left:870px;top:268px;gap:10px" aria-label="Social media links"><i></i><i></i><i></i><i></i><i></i></div>
</footer>

</body>
</html>
```